I have written a book called "Whispers from the Back Office - Uncover the trade tricks advisers bill huge fees every season for and would rather keep hidden"

This book will be sold through this webpage as an ebook. i have attached a copy of the cover of the book and I would like the website to be consistent with the look and feel of the book cover.

Target Market(s)

Business owners

Industry/Entity Type

Business

Requirements
Must have
• There has been a video produced for the promotion of this book which is yet to be completed. The video will be on ClipNest and the video needs to be prominent on the homepage.

I need to be able to manage and change the content as I wish on the website eg wordpress.

The page will need have a Coinvey purchase button

Also a 100% money back guarantee sign

Nice to have
• Friendloop plug in to show how many people like the page

Should not have
• I don't want the homepage or any of the other pages to be too cluttered

```html
<!DOCTYPE html>
<html lang="en">
<head>
<meta charset="utf-8">
<title>Whispers from the Back Office</title>
<link rel="stylesheet" href="https://fonts.googleapis.com/css2?family=Source+Sans+3:wght@300;400;600;700&display=swap">
<style>
:root{
  --sky-top:#52c8f5;
  --sky-bottom:#0f97d2;
  --sky-strip:#8adbfa;
  --ink:#111;
  --ink-soft:#333;
  --white:#fff;
  --hero-text:#e6f6fd;
  --btn:#0c6c9c;
  --btn-edge:#5ec3ea;
  --panel-border:#c9c9c9;
  --widget-head:#3b5590;
  --widget-link:#3b5998;
  --footer:#f5f4f4;
  --player:#2b2b2b;
  --gold:#e2b21a;
  --gold-dark:#b98a06;
}
*{margin:0;padding:0;box-sizing:border-box}
html,body{width:1200px;height:1148px;overflow:hidden}
body{position:relative;font-family:"Source Sans 3",sans-serif;color:var(--ink);background:var(--white)}
.hero{position:absolute;left:0;top:0;width:1200px;height:571px;background:linear-gradient(var(--sky-top),var(--sky-bottom));border-top:9px solid var(--sky-strip)}
.brand{position:absolute;left:82px;top:26px;line-height:1}
.brand-top{font-size:33px;font-weight:600;color:#0f2a3a;letter-spacing:-.3px}
.brand-main{font-size:42px;font-weight:700;color:var(--white);margin-top:2px;letter-spacing:-.3px}
.nav{position:absolute;left:581px;top:48px;display:flex;align-items:center;height:51px}
.nav a{color:var(--white);text-decoration:none;font-size:22px;padding:0 22px;border-left:1px solid rgba(255,255,255,.5);line-height:22px}
.nav a.current{background:var(--white);color:#0f2a3a;border-radius:26px;border:0;line-height:51px;padding:0 28px;margin-right:0}
.nav a.current + a{border-left:0}
.hero-art{position:absolute;left:138px;top:171px;width:330px;height:328px;border-radius:8px;background:linear-gradient(160deg,#d9dde2 0%,#9aa3ad 45%,#c05a2a 70%,#2d5fa8 100%);opacity:.9}
.hero-copy{position:absolute;left:640px;top:191px;width:480px;color:var(--white)}
.hero-copy h1{font-size:50px;font-weight:600;line-height:1;letter-spacing:-.5px}
.hero-copy h2{font-size:36px;font-weight:400;line-height:1.1;margin-top:4px}
.hero-copy p{font-size:17px;font-weight:300;color:var(--hero-text);line-height:25px;margin-top:13px;padding-left:5px}
.buy-btn{position:absolute;left:644px;top:384px;width:184px;height:49px;border-radius:6px;background:var(--btn);border:1px solid var(--btn-edge);color:var(--white);font-size:17px;font-weight:700;display:flex;align-items:center;justify-content:center;gap:6px;letter-spacing:-.3px}
.slider-arrows{position:absolute;left:1083px;top:522px}
.intro{position:absolute;left:77px;top:617px;width:320px}
.intro h3{font-size:27px;font-weight:400;letter-spacing:-.3px}
.intro h4{font-size:21px;font-weight:400;margin-top:14px}
.intro p{font-size:14.5px;line-height:22.6px;color:var(--ink-soft);margin-top:4px}
.intro p + p{margin-top:6px}
.video{position:absolute;left:428px;top:617px;width:365px}
.video h3{font-size:24px;font-weight:400}
.player{margin-top:12px;width:364px;height:260px;background:var(--white);border:1px solid #ddd;box-shadow:0 14px 22px -10px rgba(0,0,0,.25);position:relative}
.player-frame{position:absolute;left:9px;top:9px;width:346px;height:203px;background:linear-gradient(#f3f3f3,#e4e4e4)}
.player-frame .figure{position:absolute;left:88px;top:0;width:180px;height:203px;background:#111;border-radius:60px 60px 0 0}
.player-bar{position:absolute;left:0;bottom:0;width:364px;height:48px;background:var(--player);display:flex;align-items:center}
.player-bar .play{width:50px;height:48px;background:#1c1c1c;display:flex;align-items:center;justify-content:center}
.track{margin-left:8px;width:256px;height:6px;background:#8a8a8a;border-radius:3px;position:relative}
.track::after{content:"";position:absolute;left:20px;top:-4px;width:14px;height:14px;border-radius:50%;background:#eee}
.likebox{position:absolute;left:827px;top:620px;width:297px;height:288px;border:1px solid var(--panel-border);background:var(--white);font-size:11px;color:#333}
.likebox-head{height:32px;background:var(--widget-head);color:var(--white);display:flex;justify-content:space-between;align-items:center;padding:0 12px 0 10px;font-size:13px}
.likebox-head b{font-size:15px;font-weight:700}
.page-row{display:flex;gap:10px;padding:10px 12px 8px;border-bottom:1px solid #e2e2e2;margin:0 6px}
.page-icon{width:36px;height:36px;background:#222;border-radius:4px}
.page-row strong{display:block;color:var(--widget-link);font-size:15px;font-weight:600}
.page-row span a{color:var(--widget-link)}
.fan-count{padding:6px 12px 3px}
.fans{display:grid;grid-template-columns:repeat(5,48px);gap:4px 6px;padding:0 12px}
.fan i{display:block;width:48px;height:50px;background:linear-gradient(#c9b7a4,#6c5a4a)}
.fan span{display:block;text-align:center;font-size:9.5px;color:#777;margin-top:2px;white-space:nowrap;overflow:hidden}
.likebox-foot{position:absolute;left:10px;bottom:6px;display:flex;align-items:center;gap:5px;font-size:10px;color:#777}
.likebox-foot i{width:12px;height:12px;background:var(--widget-link);display:block}
.footer{position:absolute;left:0;top:979px;width:1200px;height:169px;background:var(--footer)}
.footer-nav{position:absolute;left:75px;top:38px;font-size:17.5px;color:#222}
.footer-nav span{margin:0 12px;color:#555}
.copyright{position:absolute;left:75px;top:74px;font-size:13px;color:#222}
.pay{position:absolute;left:734px;top:42px;display:flex;gap:4px}
.pay span{height:27px;border:1px solid #888;background:var(--white);font-size:11px;font-weight:600;color:#333;display:flex;align-items:center;justify-content:center;width:42px}
.pay span.wide{width:74px}
.social{position:absolute;left:825px;top:85px;display:flex;gap:6px}
.social span{width:26px;height:26px;border-radius:3px;background:#3a8fd4}
.badge{position:absolute;left:985px;top:9px;width:120px;height:120px}
</style>
</head>
<body>
<header class="hero">
  <div class="brand">
    <div class="brand-top">Whispers from</div>
    <div class="brand-main">the Back Office</div>
  </div>
  <nav class="nav">
    <a class="current" href="#">Main</a>
    <a href="#">About</a>
    <a href="#">Buy Now</a>
    <a href="#">Video</a>
    <a href="#">Contact</a>
  </nav>
  <div class="hero-art" role="img" aria-label="Laptop showing financial charts resting on a stack of colourful books"></div>
  <div class="hero-copy">
    <h1>Duis tincidunt lectus</h1>
    <h2>quis dui viverra vestibulum...</h2>
    <p>Mauris vel lacus vitae felis vestibulum volutpat. Etiam est nunc, venenatis in, tristique eu, imperdiet ac, nisl. Cum sociis natoque penatibus et magnis dis parturient montes</p>
  </div>
  <a class="buy-btn">PURCHASE BOOK NOW
    <svg width="7" height="10" viewBox="0 0 7 10"><path d="M0 0L7 5L0 10Z" fill="#fff"/></svg>
  </a>
  <svg class="slider-arrows" width="36" height="24" viewBox="0 0 36 24"><path d="M11 2L3 12L11 22M25 2L33 12L25 22" fill="none" stroke="#fff" stroke-width="3"/></svg>
</header>

<section class="intro">
  <h3>Little About My E-book</h3>
  <h4>Mauris vel lacus vitae felis</h4>
  <p>Etiam est nunc, venenatis in, tristique eu, imperdiet ac, nisl. Cum sociis natoque penatibus et magnis dis parturient montes, nascetur ridiculus mus. In iaculis facilisis massa. Etiam eu urna. Sed porta. Suspendisse quam leo, molestie sed, luctus quis, feugiat in, pede. Fusce tellus.</p>
  <p>Sed metus augue, convallis et, vehicula ut, pulvinar eu, ante. Integer orci tellus, tristique vitae, consequat nec, porta vel, lectus.</p>
</section>

<section class="video">
  <h3>Promotional Video</h3>
  <div class="player">
    <div class="player-frame" role="img" aria-label="ClipNest promotional video still of a businessman silhouette"></div>
    <div class="player-bar">
      <div class="play"><svg width="14" height="16" viewBox="0 0 14 16"><path d="M0 0L14 8L0 16Z" fill="#fff"/></svg></div>
      <div class="track"></div>
      <svg style="margin-left:14px" width="24" height="20" viewBox="0 0 24 20"><path d="M2 7H6L11 3V17L6 13H2Z" fill="none" stroke="#fff" stroke-width="1.5"/><path d="M15 6Q18 10 15 14M18 3Q23 10 18 17" fill="none" stroke="#fff" stroke-width="1.5"/></svg>
    </div>
  </div>
</section>

<aside class="likebox">
  <div class="likebox-head"><span>Find us on Friendloop</span><b>Friendloop</b></div>
  <div class="page-row">
    <div class="page-icon"></div>
    <div><strong>Ledger Widgets</strong><span>You like this. <a>Unlike</a></span></div>
  </div>
  <div class="fan-count">3,720 people like <b>Ledger Widgets</b>.</div>
  <div class="fans">
    <div class="fan"><i role="img" aria-label="Fan profile photo"></i><span>Lena</span></div>
    <div class="fan"><i role="img" aria-label="Fan profile photo"></i><span>Fenna</span></div>
    <div class="fan"><i role="img" aria-label="Fan profile photo"></i><span>Suren</span></div>
    <div class="fan"><i role="img" aria-label="Fan profile photo"></i><span>Bo</span></div>
    <div class="fan"><i role="img" aria-label="Fan profile photo"></i><span>Radim</span></div>
    <div class="fan"><i role="img" aria-label="Fan profile photo"></i><span>Kiyo</span></div>
    <div class="fan"><i role="img" aria-label="Fan profile photo"></i><span>Cam</span></div>
    <div class="fan"><i role="img" aria-label="Fan profile photo"></i><span>Mateo</span></div>
    <div class="fan"><i role="img" aria-label="Fan profile photo"></i><span>Kostas</span></div>
    <div class="fan"><i role="img" aria-label="Fan profile photo"></i><span>Mara Filo</span></div>
  </div>
  <div class="likebox-foot"><i></i>Friendloop social plugin</div>
</aside>

<footer class="footer">
  <div class="footer-nav">Main<span>/</span>About<span>/</span>Buy Now<span>/</span>Video<span>/</span>Contact</div>
  <div class="copyright">© 2013 Company Name.&nbsp; All right reserved.&nbsp; Term of Use</div>
  <div class="pay">
    <span>Paxa</span><span>Mintcard</span><span>Amerline</span><span class="wide">Coinvey</span>
  </div>
  <div class="social" aria-label="Chirpline, Linkwise, Friendloop, Circlo"><span></span><span></span><span></span><span></span></div>
  <svg class="badge" viewBox="0 0 120 120" role="img" aria-label="100% money back guarantee seal">
    <circle cx="60" cy="60" r="58" fill="var(--gold-dark)"/>
    <circle cx="60" cy="60" r="50" fill="var(--gold)"/>
    <circle cx="60" cy="60" r="36" fill="none" stroke="var(--gold-dark)" stroke-width="2"/>
  </svg>
</footer>
</body>
</html>
```